Pella's Salon (Business Cards) Needed

I need a new business card for my hair salon based in Fairfax, VA called "Pella's Salon". I have been in business at the same location for the past 15 years, and have recently remodeled the place to be a little bit more upscale and modern. Previously, my clientele's were mostly men, but now I would like to attract more female clientele into my business. I would like the design to attract the female's attention with it's modern touch, flowery, freshness with just enough information and not too compact. Simple, clean and professional is the look.
Requirements
Must Have:
- The design should include:
Business name: Pella's Salon
Hairstylist/Owner Name: Pella Marsden
Phone Number: (555) 418-6307
Website: www.pellahairstudio.example
Address: 48153 Corwin Dale Lane
Fairfax, VA 20917
FRONT CARD should include:
- Logo (Business name)
- Slogan (Your beauty, our passion)
BACK CARD should include:
- Logo (Business name)
- Hairstyle name
- Phone number
- Website
- Address
Updates
Project Deadline Extended
Reason: There were some good submission for this project, but most of the submission were poorly designed, and did not have what I want. There isn't enough designs for me to choose from and not one of it stood out to me. I would like to extend it a bit longer to see if any other designer would step up to the plate, and deliver. Thank you.
Industry/Entity Type
Hair
Requirements
Must have
- The front side of the business card should only have the business name (Pella's Salon) and slogan, (Your beauty our passion) with a creative design.
The back side of the business card should have all the business information, and creative design that matches with the front, but not identical.
The first letter (V) in (Pella's) should have a flower design connected to it, which blends into the background design.
Nice to have
- Light color scheme.
Should not have
- The front, and back should not have the same design.
Do not include illustrations of a pair of scissors, combs or any objects in the design.
The design should not take the main focus from the business name and business information. It should blend well together... if that's possible.

```html
<!DOCTYPE html>
<html lang="en">
<head>
<meta charset="utf-8">
<title>Pella's Salon – Business Cards</title>
<link href="https://fonts.googleapis.com/css2?family=Arimo:wght@400;700&family=Great+Vibes&family=Roboto:wght@300&display=swap" rel="stylesheet">
<style>
  :root {
    --stage: #2e2e2e;
    --cream: #f5eae1;
    --rose: #ff8787;
  }
  html, body {
    margin: 0;
    padding: 0;
    overflow: hidden;
  }
  body {
    width: 1091px;
    height: 1200px;
    background: var(--stage);
    position: relative;
  }
  .card {
    position: absolute;
    top: 182px;
    width: 396px;
    height: 741px;
    overflow: hidden;
  }
  .card--back { left: 124px; background: var(--cream); color: var(--rose); }
  .card--front { left: 591px; background: var(--rose); color: var(--cream); }

  .contact-head {
    position: absolute;
    top: 36px;
    left: 0;
    width: 100%;
    text-align: center;
    font-family: "Arimo", Arial, sans-serif;
  }
  .stylist-name { font-size: 15px; font-weight: 700; margin: 0; }
  .stylist-role { font-weight: 400; }
  .stylist-phone { font-size: 13.5px; font-weight: 700; margin: 9px 0 0; }

  .emblem {
    position: absolute;
    top: 190px;
    left: 123px;
    width: 150px;
    height: 150px;
  }

  .brand-name {
    position: absolute;
    top: 400px;
    left: 0;
    width: 100%;
    text-align: center;
    font-family: "Great Vibes", cursive;
    font-size: 74px;
    line-height: 1;
    margin: 0;
    font-weight: 400;
  }
  .slogan {
    position: absolute;
    top: 494px;
    left: 0;
    width: 100%;
    text-align: center;
    font-family: "Roboto", Helvetica, sans-serif;
    font-weight: 300;
    font-size: 22px;
    margin: 0;
  }

  .address-band {
    position: absolute;
    left: 0;
    bottom: 0;
    width: 100%;
    height: 81px;
    background: var(--rose);
    color: var(--cream);
    font-family: "Arimo", Arial, sans-serif;
    text-align: center;
  }
  .address-line { font-size: 12.5px; margin: 22px 0 0; }
  .website { font-size: 13px; font-weight: 700; margin: 5px 0 0; }
</style>
</head>
<body>

  <section class="card card--back" aria-label="Back of card">
    <div class="contact-head">
      <p class="stylist-name">PELLA MARSDEN - <span class="stylist-role">Hairstylist</span></p>
      <p class="stylist-phone">Phone: (555) 418-6307</p>
    </div>
    <svg class="emblem" viewBox="0 0 150 150" aria-hidden="true">
      <circle cx="75" cy="75" r="72" fill="var(--rose)"/>
    </svg>
    <h1 class="brand-name">Pella's Salon</h1>
    <p class="slogan">Your beauty, our passion</p>
    <div class="address-band">
      <p class="address-line">48153 Corwin Dale Lane, Fairfax, VA 20917</p>
      <p class="website">www.pellahairstudio.example</p>
    </div>
  </section>

  <section class="card card--front" aria-label="Front of card">
    <svg class="emblem" viewBox="0 0 150 150" aria-hidden="true">
      <circle cx="75" cy="75" r="72" fill="var(--cream)"/>
    </svg>
    <h2 class="brand-name">Pella's Salon</h2>
    <p class="slogan">Your beauty, our passion</p>
  </section>

</body>
</html>
```